Letter and Envelope Design For Harborline Realty

Please design a letter and an envelope incorporating our logo (See Attached). We are also launched a business card contest. Since we want them to match, please feel free to submit a design for both the business card and also the letter design and envelope.

Requirements
Must have
• The envelope, the letter and the business cards must match somehow connecting the designs. We want them to have something that holds them together besides the logo.

```html
<!DOCTYPE html>
<html lang="en">
<head>
<meta charset="utf-8">
<title>Harborline Realty – Letterhead and Envelope</title>
<link rel="stylesheet" href="https://fonts.googleapis.com/css2?family=Montserrat:wght@600&family=PT+Sans:wght@400;700&family=Arimo:wght@700&display=swap">
<style>
  :root {
    --brand-blue: #021a8c;
    --brand-grey: #5a5a5c;
    --paper: #f8f8f8;
    --backdrop: #e4e4e4;
    --body-text: #4a4a4a;
    --rule: #c9c9c9;
    --signature-tone: #d9d9db;
  }
  * { box-sizing: border-box; margin: 0; padding: 0; }
  html, body { width: 1200px; height: 825px; overflow: hidden; }
  body { background: var(--backdrop); position: relative; font-family: "PT Sans", sans-serif; }

  .sheet { position: absolute; background: var(--paper); overflow: hidden; }
  .sheet .wave { position: absolute; left: 0; top: 0; width: 100%; }
  .sheet .base-band { position: absolute; left: 0; bottom: 0; width: 100%; height: 8px; background: var(--brand-grey); }

  .brand { position: absolute; display: flex; flex-direction: column; align-items: center; }
  .brand-dot { width: 48px; height: 48px; border: 3px solid var(--brand-blue); border-radius: 50%; margin-bottom: 8px; }
  .brand-name { font-family: "Montserrat", sans-serif; font-weight: 600; color: var(--brand-blue); text-align: center; line-height: 1.15; }
  .brand-name .line-1 { display: block; font-size: 13.5px; letter-spacing: 1.6px; }
  .brand-name .line-2 { display: block; font-size: 10px; letter-spacing: 3.4px; }

  /* Letterhead */
  .letterhead { left: 81px; top: 78px; width: 473px; height: 668px; }
  .letterhead .brand { left: 41px; top: 23px; width: 128px; }
  .salutation { position: absolute; left: 42px; top: 191px; font-family: "Arimo", sans-serif; font-weight: 700; font-size: 11.5px; line-height: 14px; color: #1f1f3a; }
  .letter-body { position: absolute; left: 42px; top: 167px; width: 388px; font-size: 9.6px; line-height: 12.3px; color: var(--body-text); text-align: justify; }
  .letter-body p + p { margin-top: 12.3px; }
  .signature { position: absolute; left: 48px; top: 442px; width: 78px; height: 36px; background: var(--signature-tone); border-radius: 4px; }

  /* Envelope front */
  .envelope-front { left: 578px; top: 260px; width: 542px; height: 235px; }
  .envelope-front .brand { left: 34px; top: 26px; width: 130px; }
  .contact { position: absolute; left: 400px; top: 60px; font-size: 7.6px; line-height: 10px; color: var(--brand-blue); }
  .contact .address { display: flex; gap: 4px; }
  .contact .address svg { flex: none; margin-top: 1px; }
  .contact .web { margin-top: 6px; }
  .contact .web b { font-weight: 700; }
  .recipient { position: absolute; left: 36px; top: 130px; width: 209px; height: 65px; border: 1px solid #ececec; border-radius: 4px; background: #fbfbfb; }
  .recipient .to { position: absolute; left: 8px; top: 6px; font-size: 6.5px; line-height: 8px; color: var(--brand-blue); }
  .recipient .field { position: absolute; left: 8px; right: 8px; border-bottom: 1px dotted var(--rule); }
  .recipient .field-1 { top: 17px; }
  .recipient .field-2 { top: 30px; }
  .recipient .field-3 { top: 43px; }
  .recipient .field-4 { top: 56px; }

  /* Envelope back */
  .envelope-back { left: 578px; top: 510px; width: 542px; height: 236px; }
  .envelope-back .flap { position: absolute; left: 0; top: 0; }
</style>
</head>
<body>

<section class="sheet letterhead" aria-label="Letterhead">
  <svg class="wave" viewBox="0 0 473 46" height="46" preserveAspectRatio="none" aria-hidden="true">
    <path d="M0 0 H473 V27 C400 28 330 20 250 11 C170 3 80 3 0 12 Z" fill="var(--brand-blue)"/>
    <path d="M0 18 C80 5 170 6 250 13 C330 21 400 33 473 30 V39 C400 29 330 32 250 24 C170 14 80 12 0 28 Z" fill="var(--brand-grey)"/>
  </svg>

  <div class="brand">
    <span class="brand-dot"></span>
    <span class="brand-name"><span class="line-1">HARBORLINE</span><span class="line-2">REALTY</span></span>
  </div>

  <p class="salutation" style="top:141px">Dear Mr. Carter,</p>

  <div class="letter-body" style="top:170px">
    <p>Lorem Ipsum is simply dummy text of the printing and typesetting industry. Lorem Ipsum has been the industry's standard dummy text ever since the 1500s, when an unknown printer took a galley of type and scrambled it to make a type specimen book. It has survived not only five centuries, but also the leap into electronic typesetting, remaining essentially unchanged.</p>
    <p>The standard chunk of Lorem Ipsum used since the 1500s is reproduced below for those interested. Sections 1.10.32 and 1.10.33 from "de Finibus Bonorum et Malorum" by Marcellus are also reproduced in their exact original form, accompanied by English versions from the 1914 translation by L. Whitcombe</p>
    <p>Lorem Ipsum is simply dummy text of the printing and typesetting industry. Lorem Ipsum has been the industry's standard dummy text ever since the 1500s, when an unknown printer took a galley of type and scrambled it to make a type specimen book. It has survived not only five centuries, but also the leap into electronic typesetting, remaining essentially unchanged. It was popularised in the</p>
    <p>The standard chunk of Lorem Ipsum used since the 1500s is reproduced below for those interested. Sections 1.10.32 and 1.10.33 from "de Finibus Bonorum et Malorum" by Marcellus are also reproduced in their exact original form, accompanied by English versions from the 1914 translation by L. Whitcombe</p>
  </div>

  <div class="signature" role="img" aria-label="Handwritten signature of the sender"></div>
  <div class="base-band"></div>
</section>

<section class="sheet envelope-front" aria-label="Envelope front">
  <svg class="wave" viewBox="0 0 542 46" height="46" preserveAspectRatio="none" aria-hidden="true">
    <path d="M0 0 H542 V26 C460 30 380 22 290 13 C190 4 90 3 0 12 Z" fill="var(--brand-blue)"/>
    <path d="M0 18 C90 5 190 6 290 15 C380 24 460 35 542 28 V37 C460 35 380 33 290 25 C190 15 90 13 0 32 Z" fill="var(--brand-grey)"/>
  </svg>

  <div class="brand">
    <span class="brand-dot"></span>
    <span class="brand-name"><span class="line-1">HARBORLINE</span><span class="line-2">REALTY</span></span>
  </div>

  <div class="contact">
    <div class="address">
      <svg width="7" height="11" viewBox="0 0 7 11" aria-hidden="true"><path d="M3.5 0 A3.5 3.5 0 0 1 7 3.5 C7 6 3.5 11 3.5 11 C3.5 11 0 6 0 3.5 A3.5 3.5 0 0 1 3.5 0 Z M3.5 2 A1.5 1.5 0 1 0 3.5 5 A1.5 1.5 0 1 0 3.5 2 Z" fill="var(--brand-blue)" fill-rule="evenodd"/></svg>
      <span>2210 Bayview Road Ste 40<br>Port Hollis, CA 95410</span>
    </div>
    <div class="web">www.<b>harborline</b>.com</div>
  </div>

  <div class="recipient">
    <div class="to">TO</div>
    <div class="field field-1"></div>
    <div class="field field-2"></div>
    <div class="field field-3"></div>
    <div class="field field-4"></div>
  </div>

  <div class="base-band"></div>
</section>

<section class="sheet envelope-back" aria-label="Envelope back">
  <svg class="flap" width="542" height="66" viewBox="0 0 542 66" aria-hidden="true">
    <path d="M0 0 H542 L532 52 Q529 65 515 65 H27 Q13 65 10 52 Z" fill="var(--brand-blue)"/>
  </svg>
</section>

</body>
</html>
```